Design NEW business card

We would like a business card using the colour deep red wine or dark navy blue textured background (patterned or not, open to suggestions) with a high gloss debossed rose gold/copper RM Roland Mercer Jewellery business name (Provided). I have included images for your review we would like to keep our currently logo and business name on the front but you can change the layout and positioning. For the back of the card we are open to all suggestions/variations.
Business
Use our current RM Roland Mercer Jewellery logo (Provided image)

```html
<!DOCTYPE html>
<html lang="en">
<head>
<meta charset="utf-8">
<title>Roland Mercer Jewellery – Business Card</title>
<link href="https://fonts.googleapis.com/css2?family=Montserrat:wght@300;400&display=swap" rel="stylesheet">
<style>
  :root {
    --backdrop: #a8a8a8;
    --wine: #4a1422;
    --wine-deep: #350d17;
    --wine-light: #5a1a2a;
    --card-light: #f7f7f6;
    --copper: #c08a66;
    --ink: #4a4a4a;
    --muted: #a5a5a5;
  }
  * { margin: 0; padding: 0; box-sizing: border-box; }
  html, body {
    width: 1200px; height: 960px; overflow: hidden;
    background: var(--backdrop);
    font-family: "Montserrat", Arial, sans-serif;
  }
  .stage { position: relative; width: 1200px; height: 960px; }
  .card {
    position: absolute; left: 320px; width: 600px; height: 342px;
    box-shadow: 0 3px 6px rgba(0,0,0,.35);
  }
  .card--front {
    top: 108px;
    background:
      repeating-linear-gradient(45deg, rgba(255,255,255,.018) 0 2px, rgba(0,0,0,.03) 2px 4px),
      radial-gradient(ellipse at 45% 40%, var(--wine-light) 0%, var(--wine) 55%, var(--wine-deep) 100%);
  }
  .card--back { top: 493px; background: var(--card-light); }

  .brand { position: absolute; color: var(--copper); font-weight: 300; }
  .brand__mark {
    position: absolute; border: 1.5px solid var(--copper); border-radius: 50%;
  }
  .brand__name { position: absolute; white-space: nowrap; text-transform: uppercase; }
  .brand__line { position: absolute; white-space: nowrap; text-transform: uppercase; }

  .card--front .brand__mark { left: 132px; top: 80px; width: 94px; height: 94px; }
  .card--front .brand__name { left: 196px; top: 224px; font-size: 23px; letter-spacing: 6px; }
  .card--front .brand__line { left: 196px; top: 261px; font-size: 9px; letter-spacing: 28px; }

  .card--back .brand__mark { left: 54px; top: 32px; width: 72px; height: 72px; }
  .card--back .brand__name { left: 101px; top: 139px; font-size: 18px; letter-spacing: 3px; }
  .card--back .brand__line { left: 101px; top: 167px; font-size: 7px; letter-spacing: 19px; }

  .holder { position: absolute; left: 48px; top: 233px; }
  .holder__name { color: var(--copper); font-size: 18px; font-weight: 400; }
  .holder__role { color: var(--muted); font-size: 13px; font-weight: 400; margin-top: 3px; }

  .contact { position: absolute; left: 354px; top: 203px; color: var(--ink); font-size: 14px; line-height: 18px; }
  .contact__address { margin-bottom: 8px; }
  .contact__row { display: flex; align-items: center; gap: 8px; height: 19.5px; }
  .contact__icon { width: 13px; height: 13px; fill: var(--copper); flex: none; }
</style>
</head>
<body>
<main class="stage">
  <section class="card card--front" aria-label="Card front">
    <div class="brand">
      <span class="brand__mark"></span>
      <span class="brand__name">Roland Mercer</span>
      <span class="brand__line">Jewellery</span>
    </div>
  </section>

  <section class="card card--back" aria-label="Card back">
    <div class="brand">
      <span class="brand__mark"></span>
      <span class="brand__name">Roland Mercer</span>
      <span class="brand__line">Jewellery</span>
    </div>

    <div class="holder">
      <p class="holder__name">DANIEL HARPER</p>
      <p class="holder__role">CEO/FOUNDER</p>
    </div>

    <div class="contact">
      <p class="contact__address">2140 Alder Court<br>Juneau, Alaska 99801</p>
      <p class="contact__row">
        <svg class="contact__icon" viewBox="0 0 16 16" aria-hidden="true"><path d="M3.6 1.2l2.3 2.6-1.2 1.9c.9 2 2.6 3.7 4.6 4.6l1.9-1.2 2.6 2.3-1.1 2.5C7.2 14.6 1.4 8.8.7 3.3z"/></svg>
        555 218 9047
      </p>
      <p class="contact__row">
        <svg class="contact__icon" viewBox="0 0 16 16" aria-hidden="true"><path d="M1 3.5h14v9H1z" /><path d="M1 3.5l7 5 7-5" fill="none" stroke="#f7f7f6" stroke-width="1.3"/></svg>
        hello@rmjewel.com
      </p>
      <p class="contact__row">
        <svg class="contact__icon" viewBox="0 0 16 16" aria-hidden="true"><circle cx="8" cy="8" r="7"/><path d="M1 8h14M8 1c-2.5 2.5-2.5 11.5 0 14M8 1c2.5 2.5 2.5 11.5 0 14" fill="none" stroke="#f7f7f6" stroke-width="1"/></svg>
        www.rmjewel.com
      </p>
    </div>
  </section>
</main>
</body>
</html>
```